Celvara Health Group Presentation Folder, for Cancer Awareness, VERY COLORFUL AND MODERN

Presentation Folder I know pretty much what i want so it should be very eazy , I have included files from folders I use now rebrand them to my new company they will be fine, no sense re creating the wheel
Full Bleed Size
20.87" x 16.68"
53 x 42.4 cm
6260 x 5004 pixels
Document Trim Size
20.75" x 16.56"
52.7 x 42.1 cm
6225 x 4969 pixels

Low design quality

Industry/Entity Type

Medical

Font styles to use
Serif

Colors

Designer to choose colors to be used in the design.

Requirements
Must have
• really I am not looking for some one to redesign, we like our folder front page and would like to see new word information added., there are two folder front pages to choose from
• So Keep the original front page and redesign the back page and the pockets
• Can Make your Design off of one of the ones I already uploaded
Nice to have
• Keep the same color schemes, Keep the original front page and redesign the back page and the pockets
Should not have
• DO not recreate the front covers, use what I gave you and just rebrand

```html
<!DOCTYPE html>
<html lang="en">
<head>
<meta charset="utf-8">
<title>Celvara Health Group – Presentation Folder</title>
<link href="https://fonts.googleapis.com/css2?family=Raleway:wght@300;400;500;700&family=Montserrat:wght@700;800&display=swap" rel="stylesheet">
<style>
  :root{
    --backdrop:#5f5f5f;
    --paper:#ffffff;
    --navy:#1c2a6b;
    --ink:#2b2b2b;
    --green:#7cc142;
    --pink:#f29cae;
    --slate:#6f6f73;
    --guide:#5fc3e4;
    --die:#d9343a;
    --fold:#37b34a;
  }
  *{margin:0;padding:0;box-sizing:border-box}
  html,body{width:1200px;height:1000px;overflow:hidden}
  body{background:radial-gradient(ellipse at center,#6d6d6d 0%,var(--backdrop) 70%,#555 100%);font-family:"Raleway",sans-serif;position:relative}
  .dieline{position:absolute;left:0;top:0}
  .panel-guide{position:absolute;border:1px solid var(--guide)}
  .photo{position:absolute}
  .back-copy{position:absolute;left:131px;top:532px;width:420px;font-size:10.2px;line-height:12px;color:var(--ink)}
  .back-copy p{margin-bottom:10px}
  .back-copy .lead{color:var(--green);font-weight:700}
  .back-copy .motto,.back-copy .direction{color:var(--navy);font-size:11.2px;line-height:13.4px;font-weight:500}
  .title-band{position:absolute;left:600px;top:112px;width:548px;height:42px;background:var(--pink);color:#fff;font-weight:300;font-size:22px;letter-spacing:2px;text-align:center;line-height:42px;padding-left:52px}
  .subtitle-box{position:absolute;left:702px;top:154px;width:343px;height:32px;background:var(--slate);color:#fff;font-weight:300;font-size:14.4px;line-height:32px;text-align:center}
  .intro{position:absolute;left:660px;top:204px;width:428px;text-align:center;font-size:12px;line-height:14.4px;color:var(--ink);font-weight:500}
  .tag-band{position:absolute;left:600px;top:596px;width:548px;height:36px;background:var(--slate);color:#fff;font-weight:300;font-size:16px;line-height:36px;padding-left:139px}
  .seal{position:absolute;left:674px;top:610px;width:44px;height:44px;border-radius:50%;background:#fff;border:3px solid var(--navy)}
  .pocket{position:absolute;top:698px;height:238px;transform:rotate(180deg)}
  .pocket-left{left:98px;width:498px}
  .pocket-right{left:604px;width:500px}
  .brand-name{position:absolute;font-weight:700;color:var(--navy)}
  .pocket-left .brand-name{left:150px;top:180px;width:200px;text-align:center;font-size:13px}
  .division{position:absolute;left:120px;top:199px;width:260px;text-align:center;font-size:10.5px;color:var(--ink)}
  .wordmark{position:absolute;left:190px;top:98px;display:flex;align-items:center;gap:8px}
  .wordmark .dot{width:38px;height:38px;border-radius:50%;border:3px solid var(--navy)}
  .wordmark span{font-size:14px;font-weight:700;color:var(--navy);line-height:16px;width:70px}
  .pocket-copy{position:absolute;left:70px;top:46px;width:342px;color:var(--ink);font-size:6.2px;line-height:7.6px}
  .pocket-copy p{margin-bottom:2px}
  .pocket-headline{font-family:"Montserrat",sans-serif;font-weight:800;font-size:13.6px;line-height:19px;color:var(--navy);margin-top:12px}
  .pocket-headline em{font-style:normal;color:var(--green)}
</style>
</head>
<body>
<svg class="dieline" width="1200" height="1000" viewBox="0 0 1200 1000" aria-hidden="true">
  <path d="M54,70 L600,66 L1144,66 L1148,72 L1148,444 A18,18 0 0 1 1148,480 L1148,688 L1104,700 L1104,936 L644,936 Q612,936 604,700 L600,698 L596,700 Q588,936 556,936 L98,936 L98,700 L54,688 L54,480 A18,18 0 0 1 54,444 Z" fill="var(--paper)" stroke="var(--die)" stroke-width="1"/>
  <line x1="600" y1="66" x2="600" y2="698" stroke="var(--fold)" stroke-width="0.8" stroke-dasharray="3 3"/>
  <line x1="98" y1="698" x2="1104" y2="698" stroke="var(--fold)" stroke-width="0.8" stroke-dasharray="3 3"/>
  <path d="M130,716 H562 L540,900 Q538,918 520,918 H130 Z" fill="none" stroke="var(--guide)" stroke-width="0.8"/>
  <path d="M630,716 H1060 V918 H672 Q654,918 652,900 Z" fill="none" stroke="var(--guide)" stroke-width="0.8"/>
  <g stroke="var(--die)" stroke-width="0.8">
    <line x1="250" y1="803" x2="282" y2="771"/>
    <line x1="408" y1="771" x2="440" y2="803"/>
    <line x1="250" y1="848" x2="282" y2="880"/>
    <line x1="408" y1="880" x2="440" y2="848"/>
  </g>
</svg>

<div class="panel-guide" style="left:112px;top:80px;width:470px;height:602px"></div>
<div class="panel-guide" style="left:618px;top:80px;width:472px;height:602px"></div>

<div class="photo" role="img" aria-label="Three-generation family smiling together indoors" style="left:131px;top:107px;width:253px;height:141px;background:linear-gradient(135deg,#e8d6c2,#c9a98a)"></div>
<div class="photo" role="img" aria-label="Family holding hands on a rocky seashore" style="left:384px;top:107px;width:163px;height:141px;background:linear-gradient(180deg,#a9c8e2,#7d8f9c)"></div>
<div class="photo" role="img" aria-label="Family lying on green grass outdoors" style="left:131px;top:250px;width:416px;height:134px;background:linear-gradient(180deg,#b7cf7a,#6fa33d)"></div>
<div class="photo" role="img" aria-label="Family in white walking on a beach" style="left:131px;top:384px;width:226px;height:132px;background:linear-gradient(180deg,#3f8fd6,#e6dcc4)"></div>
<div class="photo" role="img" aria-label="Smiling extended family with a baby" style="left:357px;top:384px;width:190px;height:132px;background:linear-gradient(135deg,#ead9c8,#c99380)"></div>

<div class="back-copy">
  <p><span class="lead">Hereditary cancer screening</span> provides vital information to help people with a strong personal or family history of cancer understand their own risk of developing the disease. With this information, they can take steps to Potentially Prevent Cancer, Delay the Onset of Cancer or Catch it at an Earlier stage when outcomes and survival rates are Better.</p>
  <p class="motto">Don't be Afraid of the Answer: Knowledge is Power and Power Eradicates Fear. When You are Fearless, You Will Make all the Right Choices!</p>
  <p class="direction">Directions – USE any family picture I provided AND THE WORDS -Use you creativity to make it nice</p>
</div>

<div class="title-band">HEREDITARY CANCER SCREENING</div>
<div class="subtitle-box">Doctors are the Gatekeepers to Genetic Testing.</div>
<p class="intro">We have an obligation to help patients understand genetic risk and how testing can guide heath care decisions.</p>
<div class="photo" role="img" aria-label="Family sharing a meal at an outdoor table" style="left:600px;top:254px;width:548px;height:342px;background:linear-gradient(180deg,#f4f3ef 0%,#d9cdb8 55%,#a89479 100%)"></div>
<div class="tag-band">The test you order FOR your patients</div>
<div class="seal"></div>

<div class="pocket pocket-left">
  <div class="wordmark"><div class="dot"></div><span>Celvara Health Group</span></div>
  <div class="brand-name">Celvara Health Group</div>
  <div class="division">a division of Meridane Medical Sales LLC</div>
</div>

<div class="pocket pocket-right">
  <div class="pocket-copy">
    <p>There are many benefits to getting tested, regardless of the eventual result. If one of your family members — however distant — had cancer, there is a chance that you inherited a gene mutation that not only increases your personal risk of cancer, but also could be passed to the next generation. Those who are carriers of hereditary cancer gene mutations could be at risk of getting cancer earlier in life than the general population.</p>
    <p>The sooner genetic testing is done, the more likely it is that the risk can be managed appropriately.</p>
    <p>Hereditary cancer screening provides vital information to help people with a strong personal or family history of cancer understand their own risk of developing the disease. With this information, they can take steps to Potentially Prevent Cancer, Delay the Onset of Cancer or Catch it at an Earlier stage when outcomes and survival rates are Better.</p>
    <p class="pocket-headline">Identifying an inherited genetic<br>mutation has the potential to prevent cancer<br><em>and save lives.</em></p>
  </div>
</div>
</body>
</html>
```